quickdeedsale.com redesign with wireframes, white space and custom form are very important

Need a new two column design that will convert easily to mobile responsive. Lots of white space. Winning design will probably be based on header area and making the custom form stand out. I want the header to be very much like www.tallgatevk.com except the form not to go up into the header.
Here are some of the websites I really like:
www.birchdwell.com
http://ourplotpurchasedirect.com/
http://kellbrightproperty.com/

We buy homes for cash and close fast. Our target is a home seller who is desperate to sell quickly.
I have uploaded my really ugly wireframe and my logo. I also uploaded my photo for the about us box and a possible photo to use for the header.
The copy on the wireframe is what I will be using except for the about us box.

Here is the exact link for video to frame in the top left box.
https://clipvault.example/Qm38pzrtLa

0592cd
85cae6
eaf1f7
fbee3d
ec1f27

• Everything on wireframe.
• Must use Verdana font and nothing should be smaller than 12 point. Most should be in 14 point. (except maybe inside of form)

```html
<!DOCTYPE html>
<html lang="en">
<head>
<meta charset="utf-8">
<title>quickdeedsale.com – Sell Your Home For Cash</title>
<link rel="stylesheet" href="https://fonts.googleapis.com/css2?family=Noto+Sans:wght@400;700&family=Lato:ital,wght@0,400;0,700;1,400&display=swap">
<style>
:root{
  --blue:#0592cd;
  --sky:#85cae6;
  --mist:#eaf1f7;
  --red:#ec1f27;
  --ink:#111;
  --body:#666;
  --muted:#8a8a8a;
  --line:#dcdcdc;
  --band:#f3f3f3;
  --foot:#333335;
  --foot-deep:#262628;
  --white:#fff;
}
*{box-sizing:border-box;margin:0;padding:0}
html,body{width:1200px;height:2329px;overflow:hidden}
body{font-family:Verdana,"Noto Sans",sans-serif;color:var(--body);background:var(--white);position:relative}
.abs{position:absolute}
a{color:inherit;text-decoration:none}

/* header */
.site-header{position:absolute;left:0;top:0;width:1200px;height:116px;background:var(--white)}
.brand{position:absolute;left:147px;top:38px;display:flex;align-items:center;gap:10px;font-size:24px;font-weight:700;color:var(--red)}
.brand-mark{width:26px;height:26px;background:var(--red)}
.call-line{position:absolute;right:132px;top:32px;font-size:14px;color:#333;letter-spacing:.3px}
.call-line strong{font-size:17px;color:#111;font-weight:400;margin-left:6px}
.call-line .phone{color:var(--red);font-size:17px}
.main-nav{position:absolute;left:386px;top:64px;display:flex;font-size:13px;color:#777}
.main-nav a{padding:5px 10px;margin-right:26px;border-radius:4px}
.main-nav a.active{background:var(--blue);color:var(--white)}

/* hero */
.hero{position:absolute;left:0;top:116px;width:1200px;height:311px;
  background:linear-gradient(180deg,#6f6a5e 0%,#e5e2da 30%,#d8d4c8 55%,#5d6b3c 78%,#7b7b6f 100%)}
.hero-caption{position:absolute;left:307px;top:100px;width:587px;height:124px;background:rgba(235,235,235,.88);text-align:center;padding-top:18px}
.hero-caption .kicker{font-size:27px;color:var(--red);letter-spacing:.5px}
.hero-caption .title{font-size:33px;color:#111;letter-spacing:.8px;margin-top:2px}

/* shared */
.section-title{font-size:17px;color:var(--ink);letter-spacing:.4px}
.tick-list{list-style:none}
.tick-list li{display:flex;align-items:center;font-size:13px;color:var(--body);height:28px}
.tick-list svg{width:14px;height:14px;margin-right:16px;flex:none}

/* intro */
.benefits{position:absolute;left:147px;top:465px;width:510px}
.benefits .tick-list{margin-top:18px}
.benefits .tick-list li{height:36px;font-size:13.5px}
.video{position:absolute;left:147px;top:619px;width:498px;height:288px;
  background:linear-gradient(90deg,#a4dbe9 0%,#7ccbe0 45%,#a9e0ee 100%)}
.video-label{position:absolute;left:12px;top:10px;background:rgba(0,0,0,.72);color:var(--white);font-size:16px;font-weight:700;padding:4px 8px}
.video-label small{display:block;font-size:10px;font-weight:400;color:var(--sky)}
.video-tools{position:absolute;right:14px;top:10px;display:flex;flex-direction:column;gap:6px}
.video-tools span{width:40px;height:32px;background:#222;border-radius:3px;color:var(--white);font-size:8px;display:flex;align-items:flex-end;justify-content:center;padding-bottom:3px}
.video-bar{position:absolute;left:12px;right:12px;bottom:10px;height:36px;background:rgba(0,0,0,.8);border-radius:4px}
.video-bar .track{position:absolute;left:78px;right:100px;top:15px;height:6px;background:#555}
.video-bar .hd{position:absolute;right:30px;top:9px;color:var(--blue);font-size:14px;font-weight:700;font-style:italic}

.offer-form{position:absolute;left:684px;top:467px;width:370px;height:443px;background:var(--white);
  border:1px solid #e2e2e2;box-shadow:2px 3px 6px rgba(0,0,0,.25);padding:0 22px}
.offer-form h2{font-weight:400;font-size:17px;color:var(--blue);margin-top:10px;letter-spacing:.3px}
.offer-form p{font-size:13.5px;color:#555;margin-top:4px;margin-bottom:12px}
.field{display:block;width:319px;height:34px;border:1px solid #dedede;margin-bottom:10px;font-family:Lato,sans-serif;font-size:12px;color:#777;padding:9px 14px}
.submit{display:block;width:319px;height:34px;margin-top:14px;background:var(--blue);color:var(--white);font-family:Lato,sans-serif;font-size:13px;text-align:center;line-height:34px;box-shadow:0 2px 2px rgba(0,0,0,.3)}

/* about band */
.band-about{position:absolute;left:0;top:950px;width:1200px;height:482px;background:var(--band)}
.pitch{position:absolute;left:147px;top:44px;width:520px}
.pitch h2{font-weight:400;font-size:18px;color:var(--ink);line-height:23px}
.pitch p{font-size:12px;line-height:27px;margin-top:12px}
.pitch h3{font-weight:400;font-size:18px;color:var(--red);margin-top:14px;margin-bottom:10px}
.testimonials{position:absolute;left:698px;top:46px;width:356px}
.testimonials h2,.about h2{font-weight:400;font-size:20px;color:#333;letter-spacing:.3px}
.pager{position:absolute;right:2px;top:5px;display:flex;gap:2px}
.pager span{width:11px;height:11px;background:#999;border-radius:2px}
.quote{position:relative;margin-top:18px;height:114px;background:var(--white);border:1px solid #ddd;padding:18px 20px 0 34px;
  font-family:Lato,sans-serif;font-style:italic;font-size:11.5px;line-height:18px;color:#444}
.quote::after{content:"";position:absolute;left:24px;bottom:-10px;width:16px;height:16px;background:var(--white);border-right:1px solid #ddd;border-bottom:1px solid #ddd;transform:rotate(45deg)}
.quote .mark{position:absolute;left:14px;top:8px;font-size:26px;color:#aaa;font-style:normal}
.reviewer{display:flex;align-items:center;margin-top:22px}
.avatar{width:56px;height:56px;border-radius:50%;background:linear-gradient(160deg,#d9c8b4,#8d7460);margin-right:14px}
.reviewer b{display:block;font-weight:400;color:var(--red);font-size:14px}
.reviewer i{font-size:12px;color:#555}
.about{position:absolute;left:698px;top:308px;width:356px}
.about p{font-size:12px;line-height:22px;width:240px;margin-top:8px}
.about a{color:var(--red);font-size:13px}
.about-photo{position:absolute;right:0;top:-6px;width:92px;height:88px;border:3px solid var(--white);box-shadow:0 0 0 1px #ccc;
  background:linear-gradient(180deg,#4f7a56,#d6a98b 55%,#3d4b52)}

/* cities / blog */
.cities{position:absolute;left:147px;top:1470px;width:480px}
.cities h2{font-weight:400;font-size:20px;color:var(--red);line-height:24px;letter-spacing:.3px}
.cities p{font-size:12px;line-height:24px;margin-top:14px}
.cities p+p{margin-top:0}
.divider{position:absolute;left:646px;top:1512px;width:1px;height:282px;background:var(--line)}
.blog{position:absolute;left:679px;top:1472px;width:380px}
.blog h2{font-size:17px;color:var(--ink);letter-spacing:.3px;font-weight:400;margin-bottom:22px}
.post{display:flex;margin-bottom:15px}
.date{width:42px;height:54px;background:var(--blue);color:var(--white);text-align:center;flex:none;margin-right:10px;padding-top:3px}
.date b{display:block;font-size:22px;font-weight:400;line-height:26px}
.date span{font-size:9px}
.post h3{font-weight:400;font-size:15px;color:var(--ink);line-height:18px}
.post p{font-size:11px;line-height:15px;color:#555;margin-top:2px}

/* archives band */
.band-archive{position:absolute;left:0;top:1828px;width:1200px;height:210px;background:var(--band)}
.archive{position:absolute;left:147px;top:28px;width:480px}
.archive h2{font-weight:400;font-size:21px;color:#444}
.tags{display:flex;flex-wrap:wrap;gap:18px 16px;margin-top:14px;width:460px}
.tags span{background:var(--white);border:1px solid #e0e0e0;font-size:12.5px;color:#555;padding:10px 14px}
.feature{position:absolute;left:684px;display:flex;width:380px}
.feature .thumb{width:124px;height:72px;border:3px solid var(--white);box-shadow:0 0 0 1px #ccc;flex:none;margin-right:12px}
.feature h3{font-weight:400;font-size:17px;color:var(--red)}
.feature p{font-size:12px;line-height:19px;color:#666;margin-top:4px}

/* footer */
.site-footer{position:absolute;left:0;top:2038px;width:1200px;height:242px;background:var(--foot);color:#cfcfcf}
.foot-col{position:absolute;top:36px}
.foot-col h4{font-weight:400;font-size:15px;color:var(--white);letter-spacing:.5px;padding-bottom:6px;border-bottom:1px solid #bbb;display:inline-block;margin-bottom:12px}
.foot-col li{list-style:none;font-size:12px;line-height:24px}
.foot-rule{position:absolute;left:849px;top:38px;width:1px;height:112px;background:#666}
.foot-contact{position:absolute;left:876px;top:38px;font-size:12px;line-height:22px;color:#c8c8c8}
.social{display:flex;gap:14px;margin-top:12px}
.social span{width:30px;height:30px;border-radius:50%;background:#565658}
.foot-bar{position:absolute;left:0;top:2280px;width:1200px;height:49px;background:var(--foot-deep);color:var(--white);font-size:12px}
.foot-bar .copy{position:absolute;left:147px;top:17px}
.foot-bar .legal{position:absolute;right:146px;top:17px}
</style>
</head>
<body>

<header class="site-header">
  <a class="brand" href="#"><span class="brand-mark"></span>quickdeedsale.com</a>
  <div class="call-line">CALL US NIGHT &amp; WEEKENDS OK <strong>PHONE</strong> <span class="phone">: 407-555-0182</span></div>
  <nav class="main-nav">
    <a class="active" href="#">Home</a>
    <a href="#">Sell Your Home</a>
    <a href="#">How it works</a>
    <a href="#">Stop foreclosure</a>
    <a href="#">Probate</a>
    <a href="#">Contact</a>
  </nav>
</header>

<section class="hero" role="img" aria-label="Photo of a single-storey house with white siding, front porch and hedges">
  <div class="hero-caption">
    <div class="kicker">SELL YOUR HOME FOR CASH IN 8 DAYS</div>
    <div class="title">WE BUY HOUSES NATIONWIDE.</div>
  </div>
</section>

<section class="benefits">
  <h2 class="section-title">THESE ARE THE BENEFITS OF SELLING YOUR HOME TO US.</h2>
  <ul class="tick-list">
    <li><svg viewBox="0 0 14 14"><rect x="1" y="3" width="10" height="10" fill="none" stroke="#0592cd" stroke-width="1.3"/><path d="M3.5 7.5l2.5 2.5L13 2" fill="none" stroke="#0592cd" stroke-width="1.8"/></svg>You pick the closing date.</li>
    <li><svg viewBox="0 0 14 14"><rect x="1" y="3" width="10" height="10" fill="none" stroke="#0592cd" stroke-width="1.3"/><path d="M3.5 7.5l2.5 2.5L13 2" fill="none" stroke="#0592cd" stroke-width="1.8"/></svg>You pay NO commissions or fees.</li>
    <li><svg viewBox="0 0 14 14"><rect x="1" y="3" width="10" height="10" fill="none" stroke="#0592cd" stroke-width="1.3"/><path d="M3.5 7.5l2.5 2.5L13 2" fill="none" stroke="#0592cd" stroke-width="1.8"/></svg>You don't have to paint, clean or make repairs.</li>
  </ul>
</section>

<div class="video" role="img" aria-label="Video still of the company owner speaking in front of a house">
  <div class="video-label">quickdeedsale.com<small>from Dale Morrow</small></div>
  <div class="video-tools"><span>LIKE</span><span>LATER</span><span>SHARE</span><span>EMBED</span></div>
  <div class="video-bar">
    <svg class="abs" style="left:16px;top:9px" width="16" height="18" viewBox="0 0 16 18"><path d="M2 1l13 8-13 8z" fill="#fff"/></svg>
    <div class="track"></div>
    <div class="hd">HD</div>
  </div>
</div>

<form class="offer-form">
  <h2>YES, I WANT TO SELL MY HOME FAST!</h2>
  <p>Get a no obligation written offer in 36 hours</p>
  <span class="field">Your Name</span>
  <span class="field">Your Phone number</span>
  <span class="field">Your Email Address</span>
  <span class="field">Property Address including City, State &amp; Zip Code</span>
  <span class="field">Repair Needed if any</span>
  <span class="field">Asking Price</span>
  <span class="field">Comments</span>
  <span class="submit">Submit, to Get Started Selling Your Home Fast</span>
</form>

<section class="band-about">
  <div class="pitch">
    <h2>Sell your home or house fast for cash to a professional investor company. We buy Houses and close quickly.</h2>
    <p>Selling a home on your own has never been easier From Orlando to Greensboro - and all points in between- you can sell your home today without any hassles. Call 1-800-555-0147 or fill out the form below to get a written offer on your home in just 36 hours. Sell today online to people that care.</p>
    <h3>IF YOU NEED TO SELL A HOME FAST BECAUSE OF :</h3>
    <ul class="tick-list">
      <li><svg viewBox="0 0 14 14"><rect x="1" y="3" width="10" height="10" fill="none" stroke="#0592cd" stroke-width="1.3"/><path d="M3.5 7.5l2.5 2.5L13 2" fill="none" stroke="#0592cd" stroke-width="1.8"/></svg>Divorce or Bankruptcy</li>
      <li><svg viewBox="0 0 14 14"><rect x="1" y="3" width="10" height="10" fill="none" stroke="#0592cd" stroke-width="1.3"/><path d="M3.5 7.5l2.5 2.5L13 2" fill="none" stroke="#0592cd" stroke-width="1.8"/></svg>Foreclosure</li>
      <li><svg viewBox="0 0 14 14"><rect x="1" y="3" width="10" height="10" fill="none" stroke="#0592cd" stroke-width="1.3"/><path d="M3.5 7.5l2.5 2.5L13 2" fill="none" stroke="#0592cd" stroke-width="1.8"/></svg>Landlord problems - evictions with tenants okay</li>
      <li><svg viewBox="0 0 14 14"><rect x="1" y="3" width="10" height="10" fill="none" stroke="#0592cd" stroke-width="1.3"/><path d="M3.5 7.5l2.5 2.5L13 2" fill="none" stroke="#0592cd" stroke-width="1.8"/></svg>Inherited property in probate</li>
      <li><svg viewBox="0 0 14 14"><rect x="1" y="3" width="10" height="10" fill="none" stroke="#0592cd" stroke-width="1.3"/><path d="M3.5 7.5l2.5 2.5L13 2" fill="none" stroke="#0592cd" stroke-width="1.8"/></svg>Termites, mold, flood or fire damage, leaky roof</li>
      <li><svg viewBox="0 0 14 14"><rect x="1" y="3" width="10" height="10" fill="none" stroke="#0592cd" stroke-width="1.3"/><path d="M3.5 7.5l2.5 2.5L13 2" fill="none" stroke="#0592cd" stroke-width="1.8"/></svg>Moving or can't afford mortgage payments</li>
    </ul>
  </div>

  <div class="testimonials">
    <h2>TESTIMONIALS</h2>
    <div class="pager"><span></span><span></span></div>
    <div class="quote"><span class="mark">“</span>Lorem ipsum dolor sit amet, consectetueradipiscing elit, sed do eiusmod tempor incididunt ut labore et dolore magna aliqua ut enim ad minim veniam, quis nostrud exercitation ullamco laboris nisi eiusmod tempor labore. ”</div>
    <div class="reviewer">
      <div class="avatar" role="img" aria-label="Portrait of the reviewer"></div>
      <div><b>Renata Walsh</b><i>Winter Park</i></div>
    </div>
  </div>

  <div class="about">
    <h2>ABOUT US</h2>
    <p>Owned and operated in Orlando Florida since 2001. Oldest Continuous operated website in country</p>
    <a href="#">Learn More</a>
    <div class="about-photo" role="img" aria-label="Portrait of the company owner"></div>
  </div>
</section>

<section class="cities">
  <h2>SOME OF THE CITIES WHERE WE BUY HOUSES NOT ALL ARE LISTED.</h2>
  <p>These are the cities where we have an affiliate where you can sell a home fast or quickly and we buy homes: Orlando Jacksonville Ft Myers Tampa St Pete Gainesville Tallahassee Melbourne West Palm Beach Apopka Deland Kissimmee Lakeland Ocala Chicago Philadelphia Camden Atlanta Valdosta Houston Detroit Phoenix Seattle Tacoma Portland Charlotte Cincinnati San Antonio Harrisburg Virginia Beach Virginia Homes Greensboro Charleston SC Flint Rochester Lake Florida Wilmington Columbia Titusville If you don't see your city, we still probably buy homes there.</p>
  <p>These are the types of real estate that we buy: We buy nice houses and outdated problem homes. We buy in great neighborhoods and not so nice. We buy block homes and frame homes.We buy</p>
</section>
<div class="divider"></div>

<section class="blog">
  <h2>BLOG POSTS</h2>
  <article class="post"><div class="date"><b>21</b><span>APR</span></div><div><h3>Lorem ipsum dolor sit amet consectetur</h3><p>adipiscing elit sed do eiusmod tempor. incididunt ut lab ore et dolore magna aliqua ut enim ...</p></div></article>
  <article class="post"><div class="date"><b>21</b><span>APR</span></div><div><h3>Lorem ipsum dolor sit amet consectetur</h3><p>adipiscing elit sed do eiusmod tempor. incididunt ut lab ore et dolore magna aliqua ut enim ....</p></div></article>
  <article class="post"><div class="date"><b>21</b><span>APR</span></div><div><h3>Lorem ipsum dolor sit amet consectetur</h3><p>adipiscing elit sed do eiusmod tempor. incididunt ut lab ore et dolore magna aliqua ut enim ad ...</p></div></article>
</section>

<section class="band-archive">
  <div class="archive">
    <h2>Achives</h2>
    <div class="tags"><span>Sell My Home</span><span>Fast Cast For Homes</span><span>We Buy Houses</span><span>Real Estate Investor</span><span>Latest</span></div>
  </div>
  <div class="feature" style="top:25px">
    <div class="thumb" role="img" aria-label="Photo of a tidy two-storey house with a green lawn" style="background:linear-gradient(180deg,#9cc0d8,#c9c2a8 50%,#5f8a3e)"></div>
    <div><h3>We Buy Nice Pretty Houses.</h3><p>We buy in great neighborhoods and not so nice</p></div>
  </div>
  <div class="feature" style="top:107px">
    <div class="thumb" role="img" aria-label="Photo of a run-down house in need of repair" style="background:linear-gradient(180deg,#aac3d6,#9a6f5e 50%,#6d7a55)"></div>
    <div><h3>Some Ugly Ones As Well.</h3><p>We buy block homes and frame homes</p></div>
  </div>
</section>

<footer class="site-footer">
  <div class="foot-col" style="left:147px"><h4>NAVIGATION</h4><ul><li>Home</li><li>Sell Your Home</li><li>How it works</li><li>Foreclosure</li><li>Probate</li><li>Contact Us</li></ul></div>
  <div class="foot-col" style="left:338px"><h4>WHAT WE DO</h4><ul><li>About QuickDeedSale</li><li>We buy houses</li><li>Real Estate Investor</li><li>Sell My Home</li></ul></div>
  <div class="foot-col" style="left:525px"><h4>HOW IT WORKS</h4><ul><li>Blog</li><li>Testimonals</li><li>Contact Us</li><li>Who We Are</li><li>What We Do</li></ul></div>
  <div class="foot-col" style="left:707px"><h4>WHO WE ARE</h4><ul><li>Lorem ipsum</li><li>Sit Amet</li><li>Consectetur Amet</li><li>Adipistion sasit</li></ul></div>
  <div class="foot-rule"></div>
  <div class="foot-contact">
    Lorem ipsum dolor 2 - 3456<br>IP Sit Amet- Adipisicig Elit<br>Phone: +34 (0)12 555 0190<br>Email: info@quickdeedsale.com
    <div class="social"><span></span><span></span><span></span></div>
  </div>
</footer>
<div class="foot-bar">
  <span class="copy">Copyrights © 2015 QuickDeedSale.com - All Rights Reserved</span>
  <span class="legal">Privacy Policy &nbsp;&nbsp;|&nbsp;&nbsp; Terms &amp; Condition</span>
</div>

</body>
</html>
```